its a new company based in Christchurch new Zealand building computers ,repairs, upgrades and anything computers for the general public,i like bright happy colours like yellows, greens reds anything that stands out and it needs to communicant trust and security towards my new company,i have no logo yet,

Target Market(s)

target market of all ages

Industry/Entity Type

Building

Contact Information for Business Card

Byte Harbour Limited,ph-0218847261,email-tidelark77@mailvesta.test,14c marlowe cres,fenwick

```html
<!DOCTYPE html>
<html lang="en">
<head>
<meta charset="utf-8">
<title>Byte Harbour Limited — Business Card</title>
<link rel="stylesheet" href="https://fonts.googleapis.com/css2?family=Ubuntu:ital,wght@0,700;1,700&display=swap">
<style>
  :root {
    --page-bg: #eef1f4;
    --card-white: #ffffff;
    --card-grey: #eef0f3;
    --panel-blue: #1f6fd1;
    --panel-blue-light: #3d8fe8;
    --accent-green: #3cc24a;
    --accent-yellow: #ffc928;
    --brand-red: #e53935;
    --brand-text: #1f6fd1;
    --text-white: #ffffff;
    --shadow: rgba(30, 40, 60, 0.22);
  }
  html, body {
    margin: 0;
    width: 1200px;
    height: 899px;
    overflow: hidden;
    background: var(--page-bg);
    font-family: "Ubuntu", sans-serif;
  }
  .business-card {
    position: absolute;
    left: 100px;
    top: 164px;
    width: 1000px;
    height: 571px;
    border-radius: 60px;
    overflow: hidden;
    background: linear-gradient(90deg, var(--card-grey), var(--card-white) 40%);
    box-shadow: 0 18px 40px var(--shadow);
  }
  .card-art {
    position: absolute;
    inset: 0;
  }
  .brand {
    position: absolute;
    left: 60px;
    top: 232px;
    display: flex;
    align-items: center;
    gap: 14px;
  }
  .brand-dot {
    width: 22px;
    height: 22px;
    border-radius: 50%;
    background: var(--brand-red);
    flex: none;
  }
  .brand-name {
    font-weight: 700;
    font-size: 34px;
    line-height: 1.05;
    color: var(--brand-text);
    margin: 0;
  }
  .holder {
    position: absolute;
    left: 560px;
    top: 78px;
    width: 300px;
    color: var(--text-white);
    text-align: center;
  }
  .holder-name {
    font-style: italic;
    font-weight: 700;
    font-size: 32px;
    margin: 0 0 6px;
    letter-spacing: 0.5px;
  }
  .holder-role {
    font-style: italic;
    font-weight: 700;
    font-size: 24px;
    margin: 0;
    color: var(--accent-yellow);
  }
  .contact-list {
    position: absolute;
    left: 540px;
    top: 318px;
    list-style: none;
    margin: 0;
    padding: 0;
    color: var(--text-white);
    font-style: italic;
    font-weight: 700;
    font-size: 22px;
    line-height: 1.3;
  }
  .contact-list li {
    display: flex;
    align-items: flex-start;
    gap: 10px;
    margin-bottom: 10px;
  }
  .contact-icon {
    flex: none;
    width: 20px;
    height: 20px;
    margin-top: 4px;
  }
</style>
</head>
<body>
  <div class="business-card">
    <svg class="card-art" viewBox="0 0 1000 571" width="1000" height="571" aria-hidden="true">
      <defs>
        <linearGradient id="panelShade" x1="0" y1="0" x2="1" y2="1">
          <stop offset="0" stop-color="#1f6fd1"/>
          <stop offset="0.55" stop-color="#3d8fe8"/>
          <stop offset="1" stop-color="#1f6fd1"/>
        </linearGradient>
      </defs>
      <path class="blue-panel" d="M470 0 C432 190 430 380 398 571 L1000 571 L1000 0 Z" fill="url(#panelShade)"/>
      <path class="accent-line" d="M440 0 C404 190 400 380 366 571 L378 571 C412 380 416 190 452 0 Z" fill="#3cc24a"/>
    </svg>

    <div class="brand">
      <span class="brand-dot"></span>
      <p class="brand-name">Byte Harbour<br>Limited</p>
    </div>

    <div class="holder">
      <p class="holder-name">Rowan Tate</p>
      <p class="holder-role">Owner / C.E.O</p>
    </div>

    <ul class="contact-list">
      <li>
        <svg class="contact-icon" viewBox="0 0 20 20"><circle cx="10" cy="10" r="9" fill="none" stroke="#fff" stroke-width="2"/><path d="M10 4.5a3.5 3.5 0 0 0-3.5 3.5c0 2.6 3.5 7 3.5 7s3.5-4.4 3.5-7A3.5 3.5 0 0 0 10 4.5z" fill="#fff"/></svg>
        <span>14c marlowe cres,<br>fenwick</span>
      </li>
      <li>
        <svg class="contact-icon" viewBox="0 0 20 20"><circle cx="10" cy="10" r="9" fill="none" stroke="#fff" stroke-width="2"/><path d="M7 5l2 3-1.2 1.2a7 7 0 0 0 3 3L12 11l3 2-1 2c-4 0-9-5-9-9z" fill="#fff"/></svg>
        <span>0218847261</span>
      </li>
      <li>
        <svg class="contact-icon" viewBox="0 0 20 20"><circle cx="10" cy="10" r="9" fill="none" stroke="#fff" stroke-width="2"/><rect x="5" y="6.5" width="10" height="7" fill="#fff"/><path d="M5 6.5l5 4 5-4" fill="none" stroke="#1f6fd1" stroke-width="1.2"/></svg>
        <span>tidelark77@mailvesta.test</span>
      </li>
      <li>
        <svg class="contact-icon" viewBox="0 0 20 20"><circle cx="10" cy="10" r="9" fill="none" stroke="#fff" stroke-width="2"/><circle cx="10" cy="10" r="5" fill="none" stroke="#fff" stroke-width="1.5"/><path d="M5 10h10M10 5v10" stroke="#fff" stroke-width="1.2"/></svg>
        <span>www.byteharbour.test</span>
      </li>
    </ul>
  </div>
</body>
</html>
```